Water Delivery Service Website

We are working with BrivoNessé. They are a water delivery company and in need of a new website design.
Some sites to use for inspiration:
https://www.pelmoriston.example/home
https://www.quintalbrook.example/en/home3
https://www.drevik.example
https://www.tormaxel.example
Thank you for taking the time to consider designing a website for us. We are web developers based in Stockton, CA, USA. Most of our projects go through the same process. Understanding this process may help you win a project with us. We custom-code all of our websites in-house. We don’t have any requirements as to what tools you use for your design, but we prefer Figma files. For any design that we label as four-stars, we send it to the client for review. The client picks the final design they want us to use. Once we complete this process, we will continue to show additional clients all the four-star sites and purchase them later. Your designs will have multiple chances to sell. For better chances of success, we ask that you follow these guidelines.
IMAGES:
If you use any images or icons in the design, we ask that you have a link to the asset so we can purchase the image/icon. Most of the designs we submit do not have the customer’s images on them unless they have some great images. Be creative; show us the feeling you are trying to portray with your image choices. Use any royalty-free site you choose. We subscribe to Vantrel and mainly use their images, but we can purchase images outside of Vantrel.
PLEASE NOTE: we will not submit designs to clients with watermarks on the images.
FONTS:
We ask that you identify the fonts used in the design. This can be done in a message if you want. We typically use Google Fonts and Vantrel Fonts.
CONTENT:
We're always open to different content and ideas. We often submit designs with stock images so the client can see our vision. We typically take pictures after the website launch to use their images with our vision. Lorem Ipsum is fine for paragraphs, but we ask that you write the headers in correct English. We want to be able to show the vision and identify the sections of the website.
INSPIRATION:
We typically add a couple of links in the brief of websites we like to help you get started in your design.
REVISIONS:
We do not often ask for revisions of the designs unless we see something in the design that may not appeal to the client. If there are slight changes that we want to make, we do that in the development process.
FEEDBACK:
We rarely give feedback on designs during the design process. We are working on many website projects and do not have the time to provide feedback. We usually respond if your request is well thought out and asks specific questions, but a note asking “feedback, please” usually goes unanswered.

```html
<!DOCTYPE html>
<html lang="en">
<head>
<meta charset="utf-8">
<title>BrivoNessé — Water Delivery</title>
<link href="https://fonts.googleapis.com/css2?family=Montserrat:wght@500;600;700&family=Poppins:wght@400;500;600;700&display=swap" rel="stylesheet">
<style>
:root{
  --navy:#1a1b5e;
  --navy-deep:#111247;
  --blue:#1b8fd6;
  --blue-mid:#1566b3;
  --ink:#1d1d24;
  --text:#3a3a44;
  --muted:#6b6b76;
  --ice:#eef7fd;
  --mist:#e7e8ef;
  --field:#1e1e24;
  --white:#ffffff;
}
*{box-sizing:border-box;margin:0;padding:0}
html,body{width:1200px;height:4648px;overflow:hidden}
body{position:relative;background:var(--white);font-family:"Poppins",sans-serif;color:var(--text)}
.abs{position:absolute}
.heading{font-family:"Montserrat",sans-serif;font-weight:600;color:var(--ink);letter-spacing:.3px}
.accent{color:var(--blue)}
.btn{position:absolute;display:flex;align-items:center;justify-content:center;font-family:"Montserrat",sans-serif;font-weight:700;font-size:14px;color:#fff;background:linear-gradient(90deg,var(--blue-mid),var(--navy));border-radius:3px;text-transform:uppercase;letter-spacing:.3px;text-decoration:none}
.brand{display:flex;align-items:center;gap:10px;font-family:"Poppins",sans-serif;font-weight:600;font-size:38px;color:var(--blue-mid)}
.brand-dot{width:22px;height:22px;border-radius:50%;background:var(--navy)}
.eyebrow{font-family:"Montserrat",sans-serif;font-weight:600;font-size:13px;color:var(--ink);text-transform:uppercase}
.center{left:0;width:1200px;text-align:center}
.photo{position:absolute}

/* header */
.site-header{position:absolute;left:0;top:0;width:1200px;height:90px;background:#fff}
.main-nav a{position:absolute;top:38px;font-size:14px;color:var(--ink);text-decoration:none}
.main-nav a.active{font-weight:600}

/* hero */
.hero-text h2{font-family:"Montserrat",sans-serif;font-weight:600;color:#fff;font-size:22px}
.hero-text h1{font-family:"Montserrat",sans-serif;font-weight:700;color:#fff;font-size:50px;line-height:1}
.hero-text p{color:#fff;font-size:18px;line-height:28px}
.dots span{position:absolute;top:681px;width:14px;height:14px;border:1.5px solid #fff;border-radius:50%}
.dots span.on{background:var(--blue);border-color:var(--blue)}

/* services */
.card{position:absolute;top:1713px;width:309px;height:430px}
.card .photo{left:0;top:0;width:309px;height:251px}
.card-body{position:absolute;left:20px;top:209px;width:270px;height:211px;background:#fff;box-shadow:0 4px 14px rgba(0,0,0,.18);text-align:center}
.card-icon{position:absolute;left:101px;top:-38px;width:68px;height:68px;border-radius:50%;background:var(--navy);border:3px solid #fff;display:flex;align-items:center;justify-content:center}
.card-body h3{margin-top:44px;font-family:"Poppins",sans-serif;font-weight:600;font-size:16.5px;line-height:24px;color:var(--ink);white-space:nowrap;letter-spacing:-.2px}
.card-body p{margin:8px auto 0;width:240px;font-size:10.5px;line-height:17px;color:var(--text)}
.card-body .btn{left:84px;top:159px;width:102px;height:32px;font-size:10px}

/* form */
.field{position:absolute;left:294px;width:650px;background:var(--field);border-radius:3px;color:#fff;font-size:14px;display:flex;align-items:flex-start;padding:12px 0 0 14px;gap:14px}

/* footer */
.foot-col h4{font-family:"Poppins",sans-serif;font-weight:600;font-size:20px;color:var(--ink)}
.foot-col .bar{width:62px;height:3px;background:linear-gradient(90deg,var(--navy),var(--blue));margin:6px 0 12px}
.foot-col li{list-style:none;font-size:12px;color:var(--muted);line-height:26px}
.contact-row{display:flex;align-items:center;gap:14px;height:46px}
.contact-row .ic{width:28px;height:28px;border-radius:50%;border:1.5px solid var(--navy);display:flex;align-items:center;justify-content:center}
.contact-row small{display:block;font-size:9px;color:var(--muted);line-height:12px}
.contact-row b{font-weight:400;font-size:11px;color:var(--ink)}
.social span{position:absolute;top:4482px;width:24px;height:24px;border-radius:50%;border:1.5px solid var(--muted)}
</style>
</head>
<body>

<!-- Header -->
<header class="site-header">
  <div class="abs brand" style="left:112px;top:20px"><span class="brand-dot"></span>BrivoNessé</div>
  <nav class="main-nav">
    <a class="active" href="#" style="left:552px">Home</a>
    <a href="#" style="left:633px">About Me</a>
    <a href="#" style="left:735px">Services</a>
    <a href="#" style="left:828px">Sustainability</a>
  </nav>
  <a class="btn" href="#" style="left:944px;top:23px;width:144px;height:49px;font-size:14px">Contact Us</a>
</header>

<!-- Hero -->
<section>
  <div class="photo" role="img" aria-label="Smiling delivery worker in a blue shirt carrying two large water jugs outdoors" style="left:0;top:90px;width:1200px;height:730px;background:linear-gradient(120deg,#5d7a57 0%,#8aa08c 35%,#b8c6cc 60%,#c9d3da 100%)"></div>
  <div class="photo" role="img" aria-label="Navy paint splash backdrop behind headline" style="left:-40px;top:110px;width:560px;height:600px;background:radial-gradient(ellipse at 45% 45%,rgba(26,27,94,.98) 0%,rgba(26,27,94,.95) 45%,rgba(26,27,94,0) 70%)"></div>
  <div class="hero-text">
    <h2 class="abs" style="left:114px;top:255px">WELCOME TO</h2>
    <h1 class="abs" style="left:114px;top:285px">BRIVONESSÉ</h1>
    <p class="abs" style="left:117px;top:344px;width:340px">Welcome to BrivoNessé, your trusted source for premium water delivery.</p>
  </div>
  <a class="btn" href="#" style="left:117px;top:422px;width:143px;height:46px;background:var(--navy);border:1.5px solid #fff">Get a Quote</a>
  <div class="dots"><span style="left:114px"></span><span class="on" style="left:137px"></span><span style="left:160px"></span><span style="left:183px"></span></div>
  <svg class="abs" style="left:0;top:690px" width="1200" height="140" viewBox="0 0 1200 140">
    <polygon points="0,0 600,90 1200,0 1200,140 0,140" fill="#fff"/>
    <polygon points="0,30 600,110 1200,30 1200,48 600,130 0,48" fill="#1b6fc0"/>
    <polygon points="0,48 600,130 1200,48 1200,58 600,140 0,58" fill="#fff"/>
  </svg>
</section>

<!-- About -->
<section>
  <div class="photo" role="img" aria-label="Delivery worker sitting cross-legged beside water jugs in front of a large faint water drop shape" style="left:99px;top:893px;width:541px;height:487px;background:radial-gradient(ellipse at 55% 55%,#c9cfe0 0%,#e6e9f1 50%,#ffffff 80%)"></div>
  <div class="abs eyebrow" style="left:657px;top:936px">Who We Are</div>
  <h2 class="abs heading" style="left:655px;top:955px;font-size:34px">ABOUT <span class="accent">ME</span></h2>
  <div class="abs" style="left:657px;top:1008px;width:95px;height:2px;background:#c7a978"></div>
  <p class="abs" style="left:656px;top:1034px;width:458px;font-size:19px;line-height:31px;font-weight:600;color:var(--ink)">Gaerspiciatis unde <span class="accent">omse snis iste natus</span> error sseit voluptatem accusanti.</p>
  <p class="abs" style="left:656px;top:1108px;width:458px;font-size:14.3px;line-height:27.5px;text-align:justify">Gaerspiciatis unde omnis seiste natase aseus error sseit <b class="accent">voluptatem accusantium doloremque</b> laudan seftium, tsetam aseeem aperiam, eaque ipsa quae ab illo inventore veritatis et quasi architecto beatae vitae dicta sunt explicabo. Nemo enim ipsam voluptatem quia voluptas sit aspernatur aut odit aut fugit, sed quia consequuntur magni dolores eos qui ratione voluptatem sequi.</p>
  <a class="btn" href="#" style="left:656px;top:1321px;width:144px;height:47px">Learn More</a>
</section>

<!-- Services -->
<section>
  <div class="abs" style="left:0;top:1502px;width:1200px;height:800px;background:var(--ice)"></div>
  <div class="abs eyebrow center" style="top:1605px">What We Do</div>
  <h2 class="abs heading center" style="top:1627px;font-size:34px">OUR <span class="accent">SERVICES</span></h2>
  <div class="abs" style="left:548px;top:1682px;width:104px;height:2px;background:#9cc7e6"></div>

  <div class="card" style="left:114px">
    <div class="photo" role="img" aria-label="Man at home drinking a glass of water" style="background:linear-gradient(135deg,#8a7a62,#b9a98c 50%,#6f6a5a)"></div>
    <div class="card-body">
      <div class="card-icon"><svg width="30" height="34" viewBox="0 0 30 34"><rect x="7" y="8" width="16" height="24" rx="4" fill="none" stroke="#fff" stroke-width="2.5"/><rect x="11" y="2" width="8" height="6" fill="#fff"/></svg></div>
      <h3>Residential Water Delivery</h3>
      <p>Kaerspiciatis unde omnis iste natus error sit voluptatem accusantium doloremque laudantium, totam rem aperiam, eaque ipsa quaeab illo inventore.</p>
      <a class="btn" href="#">Learn More</a>
    </div>
  </div>
  <div class="card" style="left:444px">
    <div class="photo" role="img" aria-label="Woman in an office drinking a glass of water" style="background:linear-gradient(135deg,#9aa3ab,#d8dcdf 50%,#8c939b)"></div>
    <div class="card-body">
      <div class="card-icon"><svg width="34" height="34" viewBox="0 0 34 34"><rect x="5" y="9" width="10" height="20" rx="3" fill="none" stroke="#fff" stroke-width="2.5"/><rect x="17" y="9" width="10" height="20" rx="3" fill="none" stroke="#fff" stroke-width="2.5"/><circle cx="28" cy="27" r="5" fill="#fff"/></svg></div>
      <h3>Office &amp; Commercial Solutions</h3>
      <p>Kaerspiciatis unde omnis iste natus error sit voluptatem accusantium doloremque laudantium, totam rem aperiam, eaque ipsa quaeab illo inventore.</p>
      <a class="btn" href="#">Learn More</a>
    </div>
  </div>
  <div class="card" style="left:776px">
    <div class="photo" role="img" aria-label="Rows of large blue water jugs" style="background:linear-gradient(160deg,#1f5fb8,#4c9be0 50%,#1a4fa0)"></div>
    <div class="card-body">
      <div class="card-icon"><svg width="34" height="34" viewBox="0 0 34 34"><rect x="4" y="10" width="8" height="18" rx="2" fill="none" stroke="#fff" stroke-width="2.5"/><rect x="13" y="6" width="8" height="22" rx="2" fill="none" stroke="#fff" stroke-width="2.5"/><rect x="22" y="10" width="8" height="18" rx="2" fill="none" stroke="#fff" stroke-width="2.5"/></svg></div>
      <h3>Event &amp; Bulk Orders</h3>
      <p>Kaerspiciatis unde omnis iste natus error sit voluptatem accusantium doloremque laudantium, totam rem aperiam, eaque ipsa quaeab illo inventore.</p>
      <a class="btn" href="#">Learn More</a>
    </div>
  </div>
</section>

<!-- Sustainability -->
<section>
  <div class="photo" role="img" aria-label="Dark navy background of water jugs" style="left:0;top:2269px;width:1200px;height:592px;background:linear-gradient(180deg,#1a1c6a,#141559 60%,#10114a)"></div>
  <svg class="abs" style="left:0;top:2268px" width="1200" height="80" viewBox="0 0 1200 80"><polygon points="0,0 1200,0 1200,2 600,78 0,2" fill="#eef7fd"/></svg>
  <div class="abs eyebrow center" style="top:2466px;color:#fff">Eco Commitment</div>
  <h2 class="abs heading center" style="top:2488px;font-size:34px;color:#fff">SUSTAINABILITY</h2>
  <p class="abs" style="left:126px;top:2572px;width:948px;text-align:center;color:#fff;font-size:16px;line-height:28px">Gaerspiciatis unde omnis seiste natase aseus error sseit <b>voluptatem accusantium doloremque</b> laudan seftium, tsetam aseeem aperiam, eaque ipsa quae ab illo inventore veritatis et quasi architecto beatae vitae dicta sunt explicabo. Nemo enim ipsam voluptatem quia voluptas sit aspernatur aut odit aut fugit, sed quia consequuntur magni dolores eos qui ratione voluptatem sequi.</p>
  <div class="photo" role="img" aria-label="Filled water bottles on a bottling line" style="left:114px;top:2744px;width:465px;height:352px;background:linear-gradient(180deg,#cfe4f4,#5aa2dc 55%,#1f5ea8)"></div>
  <div class="photo" role="img" aria-label="Large blue water jugs close up" style="left:619px;top:2744px;width:466px;height:352px;background:linear-gradient(160deg,#0f2a66,#2f7fd0 50%,#103a80)"></div>
  <div class="abs" style="left:114px;top:3102px;width:465px;text-align:center;font-size:21px;font-weight:600;color:var(--ink)">100% Recyclable Packaging</div>
  <div class="abs" style="left:619px;top:3102px;width:466px;text-align:center;font-size:21px;font-weight:600;color:var(--ink)">Sustainable Sourcing &amp; Filtration</div>
</section>

<!-- Contact -->
<section>
  <div class="abs eyebrow center" style="top:3233px">Get In Touch</div>
  <h2 class="abs heading center" style="top:3253px;font-size:34px">CONTACT <span class="accent">US</span></h2>
  <p class="abs" style="left:200px;top:3330px;width:800px;text-align:center;font-size:16px;line-height:25px">We're here to help! Whether you have questions about our services, need assistance with an order, or want to discuss custom water solutions, our team is ready to assist you.</p>
  <div class="field" style="top:3402px;height:42px"><svg width="16" height="16" viewBox="0 0 16 16"><circle cx="8" cy="5" r="3.5" fill="#1b8fd6"/><path d="M1 16c0-4 3-6 7-6s7 2 7 6z" fill="#1b8fd6"/></svg>Your Name</div>
  <div class="field" style="top:3462px;height:42px"><svg width="18" height="14" viewBox="0 0 18 14"><rect x="1" y="1" width="16" height="12" rx="1" fill="#1b8fd6"/><path d="M1 2l8 6 8-6" stroke="#1e1e24" stroke-width="1.5" fill="none"/></svg>Email</div>
  <div class="field" style="top:3523px;height:42px"><svg width="16" height="16" viewBox="0 0 16 16"><path d="M3 1l3 3-2 2c1 2 3 4 6 6l2-2 3 3-2 3C7 15 1 9 1 3z" fill="#1b8fd6"/></svg>Phone Number</div>
  <div class="field" style="top:3583px;height:125px"><svg width="18" height="16" viewBox="0 0 18 16"><rect x="1" y="1" width="12" height="9" rx="1" fill="#1b8fd6"/><rect x="5" y="5" width="12" height="9" rx="1" fill="#1b8fd6" stroke="#1e1e24"/></svg>Write &nbsp;A Message</div>
  <a class="btn" href="#" style="left:527px;top:3738px;width:144px;height:47px;background:var(--blue-mid)">Send Message</a>
</section>

<!-- Call to action -->
<section>
  <div class="abs" style="left:0;top:4115px;width:1200px;height:533px;background:var(--mist)"></div>
  <div class="abs" style="left:173px;top:3935px;width:854px;height:318px;background:var(--navy);border-radius:3px"></div>
  <h2 class="abs" style="left:238px;top:3975px;width:420px;font-family:'Montserrat',sans-serif;font-weight:600;font-size:30px;line-height:38px;color:#fff">STAY HYDRATED WITH BRIVONESSÉ</h2>
  <p class="abs" style="left:238px;top:4066px;width:350px;font-size:14.5px;line-height:23px;color:#fff">Join thousands of happy customers who trust BrivoNessé for their hydration needs. Sign up today and experience the luxury of pure, fresh water—delivered to you</p>
  <a class="btn" href="#" style="left:238px;top:4173px;width:130px;height:43px;background:var(--blue-mid);font-size:12px">Send Message</a>
  <div class="photo" role="img" aria-label="Delivery worker carrying a water jug on his shoulder" style="left:690px;top:3853px;width:210px;height:400px;background:linear-gradient(180deg,rgba(110,170,220,.0),#2a6fc4 35%,#1a4f9e)"></div>
</section>

<!-- Footer -->
<footer>
  <div class="abs brand" style="left:141px;top:4388px;font-size:36px"><span class="brand-dot"></span>BrivoNessé</div>
  <div class="social"><span style="left:223px"></span><span style="left:259px"></span><span style="left:293px"></span></div>
  <div class="abs foot-col" style="left:397px;top:4354px">
    <h4>Quick Links</h4><div class="bar"></div>
    <ul><li>Home</li><li>About Me</li><li>Services</li><li>Sustainability</li><li>Contact Us</li></ul>
  </div>
  <div class="abs foot-col" style="left:606px;top:4354px">
    <h4>Links</h4><div class="bar"></div>
    <ul><li>Shipping and Delivery</li><li>Order tracking</li><li>Refund and Returns Policy</li><li>Terms &amp; Conditions</li><li>Contact Us</li></ul>
  </div>
  <div class="abs foot-col" style="left:838px;top:4354px">
    <h4>Contact Us</h4><div class="bar"></div>
    <div class="contact-row"><span class="ic"><svg width="12" height="12" viewBox="0 0 16 16"><path d="M3 1l3 3-2 2c1 2 3 4 6 6l2-2 3 3-2 3C7 15 1 9 1 3z" fill="#1a1b5e"/></svg></span><div><small>Call Us</small><b>+1 (555) 014 2290</b></div></div>
    <div class="contact-row"><span class="ic"><svg width="12" height="10" viewBox="0 0 18 14"><rect x="1" y="1" width="16" height="12" fill="#1a1b5e"/><path d="M1 2l8 6 8-6" stroke="#fff" stroke-width="1.5" fill="none"/></svg></span><div><small>Email</small><b>hello@brivonesse.example</b></div></div>
    <div class="contact-row"><span class="ic"><svg width="10" height="13" viewBox="0 0 10 14"><path d="M5 0C2 0 0 2 0 5c0 4 5 9 5 9s5-5 5-9C10 2 8 0 5 0z" fill="#1a1b5e"/><circle cx="5" cy="5" r="2" fill="#fff"/></svg></span><div><small>Address</small><b>218 Larkfield Row, Ashmere, CA 90000</b></div></div>
  </div>
  <div class="abs" style="left:112px;top:4585px;width:976px;height:1px;background:#b8b9c4"></div>
  <div class="abs center" style="top:4607px;font-size:12px;color:var(--text)">© Copyright 2025. All rights reserved.</div>
</footer>

</body>
</html>
```